Website Design for a holiday home letting busines

We require a redesign of our present website www.pinebrookstays.com. We want the website to stand out and look professional and clean to make holiday hunters want to book a caravan or lodge holiday with us. Our logo is red however we DO NOT want the website to be red. We want a natural colour scheme.

The final design should communicate that we are a professional company to book with.

On the home page we require;
Overview of company
Photo
Search box for holiday (check in)
Late Deals
Reviews
News

We would like the following pages designed; home page, available dates page, caravans page, content page.

The website should be responsive for smart phones. One website I do like is http://www.verdoliso.be/nl/

Target Market(s)

Families

Industry/Entity Type

Travel

Number of Pages Required

5+ page

Font styles to use
Serif

Requirements
Must have
• The project must be responsive for mobile phones and tablets.
• Ability to search for holiday home holidays
• We want a natural colour scheme.
Nice to have
• A style we like is http://www.verdoliso.be/nl/
Should not have
• Do not use red as a colour for the website. Our logo is red so this is the only time we want this used.

```html
<!DOCTYPE html>
<html lang="en">
<head>
<meta charset="utf-8">
<title>Pinebrook Stays – Private Holiday Rentals</title>
<link rel="stylesheet" href="https://fonts.googleapis.com/css2?family=Open+Sans:wght@400;600;700;800&display=swap">
<style>
:root{
  --orange:#e8922a;
  --orange-dark:#cf7a15;
  --teal:#0e5672;
  --teal-deep:#083246;
  --ink:#2f3a40;
  --muted:#7a858b;
  --white:#ffffff;
}
*{box-sizing:border-box;margin:0;padding:0}
html,body{width:1200px;height:2840px;overflow:hidden}
body{font-family:"Open Sans",Arial,sans-serif;color:var(--ink);background:var(--white)}
.page{position:relative;width:1200px;height:2840px;overflow:hidden}
.abs{position:absolute}

.topbar{left:0;top:0;width:1200px;height:30px;background:rgba(8,50,70,.55);color:#e8f2f6;font-size:11px;display:flex;align-items:center;justify-content:space-between;padding:0 110px;z-index:3}
.topbar span{margin-right:22px}
.topbar nav a{color:#e8f2f6;text-decoration:none;margin-left:26px}

.header{left:100px;top:30px;width:1000px;height:62px;background:var(--white);display:flex;align-items:center;justify-content:space-between;padding:0 22px;z-index:3;box-shadow:0 2px 8px rgba(0,0,0,.15)}
.brand{display:flex;align-items:center;gap:10px;font-size:19px;font-weight:700;color:#c8372d;white-space:nowrap}
.brand-dot{width:22px;height:22px;border-radius:50%;background:#c8372d}
.mainnav{white-space:nowrap}
.mainnav a{font-size:10.5px;font-weight:700;color:var(--ink);text-decoration:none;text-transform:uppercase;margin-left:20px}

.hero{left:0;top:0;width:1200px;height:720px;background:linear-gradient(180deg,#5aa4d3 0%,#8cc6e4 30%,#4d9fb8 48%,#cdb78e 62%,#b79c72 100%)}
.hero-circle{left:560px;top:130px;width:330px;height:330px;border-radius:50%;border:6px solid var(--white);background:radial-gradient(circle at 40% 40%,#e9d9bf,#8fb7c9 70%);box-shadow:0 6px 18px rgba(0,0,0,.25)}
.hero-thumb{left:415px;top:230px;width:170px;height:150px;border-radius:50%;border:5px solid var(--white);background:radial-gradient(circle,#d9b98c,#8a6a48)}
.hero-copy{left:100px;top:262px;color:var(--white)}
.hero-copy h1{font-size:34px;font-weight:800;line-height:1.05;text-transform:uppercase;letter-spacing:.5px;text-shadow:0 2px 6px rgba(0,0,0,.3)}
.hero-copy h1 small{display:block;font-size:23px;font-weight:700}
.hero-copy p{font-size:12px;line-height:1.5;margin:12px 0 16px;width:260px}
.btn{display:inline-block;background:var(--orange);color:var(--white);font-size:10.5px;font-weight:700;text-transform:uppercase;padding:10px 18px;border-radius:2px}

.search{left:100px;top:566px;width:460px;height:104px;background:rgba(255,255,255,.9);box-shadow:0 4px 12px rgba(0,0,0,.2)}
.search h3{background:var(--teal);color:var(--white);font-size:12px;font-weight:700;text-transform:uppercase;padding:10px 16px}
.search-row{display:flex;gap:10px;padding:16px}
.field{height:28px;border:1px solid #c9d0d4;background:var(--white);font-size:10px;color:var(--muted);padding:7px 10px;flex:1}
.search .go{width:40px;height:28px;background:var(--orange)}
.chat{left:1122px;top:606px;width:78px;height:44px;background:var(--orange);color:var(--white);font-size:10px;font-weight:700;text-align:center;padding-top:8px;line-height:1.3}

.wood{left:0;top:720px;width:1200px;height:740px;background:linear-gradient(180deg,#9a7552 0%,#7b5a3e 45%,#6b4d34 100%)}
.section-title{font-size:19px;font-weight:800;text-transform:uppercase;color:var(--white)}
.caravans-title{left:100px;top:700px;width:1000px;height:46px;background:rgba(60,40,25,.55);padding:12px 18px}

.cards{display:flex;gap:22px}
.card{width:232px;background:var(--white);padding:10px;box-shadow:0 3px 10px rgba(0,0,0,.2)}
.card .photo{height:200px;background:linear-gradient(160deg,#e8dcc6,#a88b66)}
.card .photo.pool{background:linear-gradient(160deg,#3d6f8f,#1d3d55)}
.card h4{font-size:11.5px;font-weight:800;color:var(--orange);text-transform:uppercase;margin:14px 0 8px}
.spec{display:grid;grid-template-columns:1fr 1fr;font-size:9.5px;color:var(--muted);row-gap:7px}
.spec b{color:var(--orange-dark);font-weight:600}
.card .btn{display:block;text-align:center;margin-top:16px}
.caravan-cards{left:115px;top:760px}

.feeds{left:100px;top:1200px;width:1000px;display:flex;gap:40px;color:#f1e8dc}
.feed{flex:1}
.feed h3{font-size:13px;font-weight:800;color:var(--white);text-transform:uppercase;border-bottom:1px solid rgba(255,255,255,.25);padding-bottom:8px;margin-bottom:12px;display:flex;justify-content:space-between}
.feed h3 i{font-style:normal;font-size:11px;opacity:.7}
.feed h5{font-size:10px;font-weight:700;color:var(--orange);text-transform:uppercase}
.feed .meta{font-size:9px;opacity:.75;margin:2px 0 8px}
.feed p{font-size:10px;line-height:1.6}
.fb{display:flex;gap:10px}
.avatar{width:44px;height:44px;flex:none;background:#c5b49c}

.deals-title{left:100px;top:1492px;color:var(--teal)}
.deals-rule{left:100px;top:1528px;width:1000px;height:1px;background:#dcdcdc}
.deal-cards{left:115px;top:1550px}
.deal-cards .card{box-shadow:0 2px 8px rgba(0,0,0,.14)}
.deal-cards .photo{height:200px}

.about{left:0;top:1960px;width:1200px;height:520px;background:linear-gradient(100deg,#f6f1ea 0%,#f6f1ea 38%,#bfd9e6 55%,#d9c49e 82%,#c6a983 100%)}
.about-copy{left:100px;top:2080px;width:380px}
.about-copy h2{font-size:20px;font-weight:800;color:var(--teal);text-transform:uppercase;margin-bottom:14px}
.about-copy p{font-size:11px;line-height:1.7;color:var(--ink);margin-bottom:12px}

.footer{left:0;top:2480px;width:1200px;height:320px;background:var(--teal);color:#d6e7ee;padding:40px 100px;display:flex;gap:60px}
.footer h4{font-size:12px;font-weight:800;color:var(--white);text-transform:uppercase;margin-bottom:12px}
.footer p,.footer li{font-size:10.5px;line-height:1.75;list-style:none}
.col-news{width:280px}
.col-news input{display:block;width:220px;height:26px;border:none;margin:8px 0;padding:0 8px;font:inherit;font-size:10px}
.col-contact{width:220px}
.contact-line{display:flex;align-items:center;gap:8px;font-size:10.5px;margin-top:6px}
.sitemap{display:flex;gap:50px}
.bottombar{left:0;top:2800px;width:1200px;height:40px;background:var(--teal-deep);color:#a9c3ce;font-size:10px;display:flex;align-items:center;justify-content:space-between;padding:0 100px}
.social{display:flex;gap:8px}
.social span{width:22px;height:22px;border-radius:50%;background:#2b6f8c}
</style>
</head>
<body>
<div class="page">

  <div class="abs hero" role="img" aria-label="Beach holiday scene with palm trees, blue sea and sand"></div>
  <div class="abs hero-circle" role="img" aria-label="Family enjoying a day on the beach"></div>
  <div class="abs hero-thumb" role="img" aria-label="Bright bedroom interior of a holiday lodge"></div>

  <div class="abs topbar">
    <div><span>☎ 01632 480 215</span><span>hello@pinebrookstays.com</span></div>
    <nav><a>Admin</a><a>News</a><a>Reviews</a><a>Contact</a></nav>
  </div>

  <header class="abs header">
    <div class="brand"><span class="brand-dot"></span>Pinebrook Stays</div>
    <nav class="mainnav">
      <a>Caravans &amp; Lodges</a><a>Late Deals</a><a>Our Holidays</a><a>Payment Plans</a><a>Larkmoor Holiday Park</a><a>Local Attractions</a>
    </nav>
  </header>

  <div class="abs hero-copy">
    <h1>Private<small>Holiday Rentals</small></h1>
    <p>Quality lodge &amp; caravan holidays at Larkmoor Holiday Park, booked direct with us.</p>
    <span class="btn">More Details</span>
  </div>

  <div class="abs search">
    <h3>Search for Holidays</h3>
    <div class="search-row">
      <div class="field">Check in date</div>
      <div class="field">Number of nights</div>
      <div class="go"></div>
    </div>
  </div>
  <div class="abs chat">Live Chat<br>Online</div>

  <div class="abs wood" role="img" aria-label="Warm wooden deck texture background"></div>
  <div class="abs caravans-title"><h2 class="section-title">List of Caravans and Lodges</h2></div>

  <div class="abs cards caravan-cards">
    <div class="card"><div class="photo" role="img" aria-label="Lodge bedroom"></div><h4>The Bramblewood</h4>
      <div class="spec"><span>Caravan type</span><b>Lodge</b><span>Sleeps</span><b>6</b><span>Bedrooms</span><b>3</b></div><span class="btn">View More Details</span></div>
    <div class="card"><div class="photo" role="img" aria-label="Caravan bedroom"></div><h4>The Bramblewood</h4>
      <div class="spec"><span>Caravan type</span><b>Lodge</b><span>Sleeps</span><b>6</b><span>Bedrooms</span><b>3</b></div><span class="btn">View More Details</span></div>
    <div class="card"><div class="photo pool" role="img" aria-label="Park pool at night"></div><h4>The Bramblewood</h4>
      <div class="spec"><span>Caravan type</span><b>Lodge</b><span>Sleeps</span><b>6</b><span>Bedrooms</span><b>3</b></div><span class="btn">View More Details</span></div>
    <div class="card"><div class="photo" role="img" aria-label="Lodge living room"></div><h4>The Bramblewood</h4>
      <div class="spec"><span>Caravan type</span><b>Lodge</b><span>Sleeps</span><b>6</b><span>Bedrooms</span><b>3</b></div><span class="btn">View More Details</span></div>
  </div>

  <section class="abs feeds">
    <div class="feed">
      <h3>Latest Reviews <i>‹ ›</i></h3>
      <h5>Harriet Calloway</h5>
      <div class="meta">Stayed in The Bramblewood</div>
      <p>Lovely lodge in a quiet corner of the park. Clean, warm and well equipped, the kids loved the pool and beach. We will be booking again next summer.</p>
    </div>
    <div class="feed">
      <h3>Blog Posts <i>‹ ›</i></h3>
      <h5>Summer breaks now open</h5>
      <div class="meta">Posted 12 April</div>
      <p>Our summer dates are now live. Book early to secure the best lodges for school holidays, with short breaks and weekly stays on offer.</p>
    </div>
    <div class="feed">
      <h3>Campfire Feed <i>‹ ›</i></h3>
      <div class="fb"><div class="avatar" role="img" aria-label="Profile picture"></div>
        <div><h5>Pinebrook Stays</h5><div class="meta">Shared a new update</div></div></div>
      <p>Sunny days ahead on the coast. A few late availability lodges remain for June, message us for details.</p>
    </div>
  </section>

  <h2 class="abs section-title deals-title">Late Deals</h2>
  <div class="abs deals-rule"></div>
  <div class="abs cards deal-cards">
    <div class="card"><div class="photo" role="img" aria-label="Caravan bedroom"></div><h4>The Seawhistle</h4>
      <div class="spec"><span>Friday 3 June, 3 nights</span><b>£299</b><span>Sleeps</span><b>6</b><span>Bedrooms</span><b>3</b></div><span class="btn">View More Details</span></div>
    <div class="card"><div class="photo" role="img" aria-label="Caravan bedroom"></div><h4>The Seawhistle</h4>
      <div class="spec"><span>Friday 3 June, 3 nights</span><b>£299</b><span>Sleeps</span><b>6</b><span>Bedrooms</span><b>3</b></div><span class="btn">View More Details</span></div>
    <div class="card"><div class="photo" role="img" aria-label="Caravan lounge"></div><h4>The Seawhistle</h4>
      <div class="spec"><span>Friday 3 June, 3 nights</span><b>£299</b><span>Sleeps</span><b>6</b><span>Bedrooms</span><b>3</b></div><span class="btn">View More Details</span></div>
    <div class="card"><div class="photo" role="img" aria-label="Caravan bedroom"></div><h4>The Seawhistle</h4>
      <div class="spec"><span>Friday 3 June, 3 nights</span><b>£299</b><span>Sleeps</span><b>6</b><span>Bedrooms</span><b>3</b></div><span class="btn">View More Details</span></div>
  </div>

  <div class="abs about" role="img" aria-label="Sunny beach with thatched parasols and loungers"></div>
  <div class="abs about-copy">
    <h2>About Lodge and Caravan</h2>
    <p>Would you like to book a 2015 caravan or lodge holiday at Larkmoor Holiday Park? Then you are in the right place.</p>
    <p>We have quality lodges and caravans to let, all privately owned and cared for, with friendly service from first enquiry to the day you leave.</p>
    <span class="btn">View More Details</span>
  </div>

  <footer class="abs footer">
    <div class="col-news">
      <h4>Newsletter Signup</h4>
      <p>Get our latest deals straight to your inbox.</p>
      <input placeholder="Enter your name">
      <input placeholder="Enter your email">
      <span class="btn">Sign Up</span>
    </div>
    <div class="col-contact">
      <h4>Contact Information</h4>
      <p>Pinebrook Stays<br>Larkmoor Holiday Park<br>Larkmoor Lane, Eastholme<br>EH4 7QP</p>
      <div class="contact-line"><svg width="12" height="12" viewBox="0 0 24 24"><path fill="#e8922a" d="M6.6 10.8a15 15 0 0 0 6.6 6.6l2.2-2.2a1 1 0 0 1 1-.25 11.4 11.4 0 0 0 3.6.57 1 1 0 0 1 1 1V20a1 1 0 0 1-1 1A17 17 0 0 1 3 4a1 1 0 0 1 1-1h3.5a1 1 0 0 1 1 1c0 1.25.2 2.45.57 3.57a1 1 0 0 1-.25 1z"/></svg>01632 480 215</div>
      <div class="contact-line"><svg width="12" height="12" viewBox="0 0 24 24"><path fill="#e8922a" d="M2 5h20v14H2z"/><path fill="none" stroke="#0e5672" stroke-width="2" d="M2 5l10 8 10-8"/></svg>hello@pinebrookstays.com</div>
    </div>
    <div>
      <h4>Sitemap</h4>
      <div class="sitemap">
        <ul><li>Home</li><li>About us</li><li>Caravans &amp; Lodges</li><li>Late Deals</li><li>Our Holidays</li><li>Payment Plans</li><li>Larkmoor Park</li><li>Local Attractions</li></ul>
        <ul><li>Reviews</li><li>Blog</li><li>Owners Area</li><li>Terms &amp; Conditions</li><li>Cancellation Policy</li><li>Privacy Policy</li><li>Contact</li><li>Booking FAQs</li></ul>
      </div>
    </div>
  </footer>
  <div class="abs bottombar">
    <span>Copyright © 2015 Pinebrook Stays. All rights reserved.</span>
    <div class="social"><span></span><span></span><span></span></div>
  </div>

</div>
</body>
</html>
```